Modern Business Card

Modern professional business card with more than just logo and demographic info. Something memorable.

We are a trendy/modern chiropractic group with an emphasis on neurology, hence the minimalist-type brain logo. We want to convey that modern and technical aspect with professionalism and the elite nature of our practice environment.

```html
<!DOCTYPE html>
<html lang="en">
<head>
<meta charset="utf-8">
<title>Northline Chiropractic – Business Card</title>
<link href="https://fonts.googleapis.com/css2?family=Montserrat:wght@600;700&family=Roboto:wght@400&display=swap" rel="stylesheet">
<style>
  :root {
    --stage: #2a2a2a;
    --blue: #4a82c3;
    --blue-light: #5e93cf;
    --ink: #1c1c1c;
    --grey-text: #4a4a4a;
    --graphite: #3d3d3d;
    --paper: #ffffff;
  }
  * { margin: 0; padding: 0; box-sizing: border-box; }
  html, body { width: 1200px; height: 900px; overflow: hidden; }
  body {
    background: var(--stage);
    font-family: "Roboto", Arial, sans-serif;
    position: relative;
  }
  .card {
    position: absolute;
    left: 250px;
    width: 700px;
    height: 400px;
    overflow: hidden;
  }
  /* Back side */
  .card-back {
    top: 38px;
    background: linear-gradient(110deg, var(--blue) 0%, var(--blue) 45%, var(--blue-light) 100%);
    display: flex;
    align-items: center;
    justify-content: center;
  }
  .brand {
    display: flex;
    align-items: center;
    gap: 16px;
    font-family: "Montserrat", Arial, sans-serif;
    font-weight: 600;
    letter-spacing: 0.04em;
    text-transform: uppercase;
    line-height: 1.1;
  }
  .brand-mark { width: 18px; height: 18px; border-radius: 50%; flex: none; }
  .card-back .brand { color: var(--paper); font-size: 36px; }
  .card-back .brand-mark { background: var(--paper); width: 26px; height: 26px; }

  /* Front side */
  .card-front { top: 466px; background: var(--paper); }
  .card-front .brand {
    position: absolute; left: 44px; top: 44px;
    color: var(--ink); font-size: 22px; gap: 12px;
  }
  .card-front .brand-mark { background: var(--blue); }
  .divider {
    position: absolute; left: 0; top: 212px;
    width: 560px; height: 2px; background: var(--blue);
  }
  .contact {
    position: absolute; left: 44px; top: 228px;
    color: var(--grey-text); font-size: 16px; line-height: 21px;
    list-style: none;
  }
  .contact li { display: flex; align-items: center; gap: 8px; }
  .contact .address { padding-left: 0; }
  .contact svg { width: 13px; height: 13px; fill: var(--blue); flex: none; }
  .person {
    position: absolute; right: 52px; top: 166px; text-align: right;
  }
  .person-name {
    font-family: "Montserrat", Arial, sans-serif; font-weight: 700;
    color: var(--blue); font-size: 28px; letter-spacing: 0.02em;
  }
  .person-role { color: var(--grey-text); font-size: 18px; margin-top: 6px; }
  .edge-tab {
    position: absolute; right: 0; top: 205px;
    width: 22px; height: 52px; background: var(--blue);
  }
  .base-band { position: absolute; left: 0; bottom: 0; width: 700px; height: 22px; }
</style>
</head>
<body>
  <section class="card card-back" aria-label="Card back">
    <div class="brand"><span class="brand-mark"></span><span>Northline<br>Chiropractic</span></div>
  </section>

  <section class="card card-front" aria-label="Card front">
    <div class="brand"><span class="brand-mark"></span><span>Northline<br>Chiropractic</span></div>
    <div class="divider"></div>
    <ul class="contact">
      <li class="address">18 Carden Avenue</li>
      <li class="address">Westbrook, Lakeside, 4120</li>
      <li><svg viewBox="0 0 24 24"><path d="M6.6 10.8a15 15 0 0 0 6.6 6.6l2.2-2.2a1 1 0 0 1 1-.25 11.4 11.4 0 0 0 3.6.57 1 1 0 0 1 1 1V20a1 1 0 0 1-1 1A17 17 0 0 1 3 4a1 1 0 0 1 1-1h3.5a1 1 0 0 1 1 1c0 1.25.2 2.45.57 3.57a1 1 0 0 1-.25 1z"/></svg>+120 5550 1847</li>
      <li><svg viewBox="0 0 24 24"><path d="M7 1h10a2 2 0 0 1 2 2v18a2 2 0 0 1-2 2H7a2 2 0 0 1-2-2V3a2 2 0 0 1 2-2zm0 3v14h10V4zm5 15.5a1 1 0 1 0 0 2 1 1 0 0 0 0-2z"/></svg>+965 5550 2376</li>
      <li><svg viewBox="0 0 24 24"><path d="M2 5h20v14H2zm2 2v.4l8 5 8-5V7zm0 2.8V17h16V9.8l-8 5z"/></svg>info@northlinechiro.com</li>
      <li><svg viewBox="0 0 24 24"><path d="M12 2a10 10 0 1 0 0 20 10 10 0 0 0 0-20zm6.9 6h-3a15 15 0 0 0-1.3-3.6A8 8 0 0 1 18.9 8zM12 4c.8 1.2 1.5 2.5 1.9 4h-3.8c.4-1.5 1.1-2.8 1.9-4zM4.3 14a8 8 0 0 1 0-4h3.4a16 16 0 0 0 0 4zm.8 2h3a15 15 0 0 0 1.3 3.6A8 8 0 0 1 5.1 16zm3-8h-3a8 8 0 0 1 4.3-3.6A15 15 0 0 0 8.1 8zM12 20c-.8-1.2-1.5-2.5-1.9-4h3.8c-.4 1.5-1.1 2.8-1.9 4zm2.3-6H9.7a14 14 0 0 1 0-4h4.6a14 14 0 0 1 0 4zm.3 5.6a15 15 0 0 0 1.3-3.6h3a8 8 0 0 1-4.3 3.6zm1.7-5.6a16 16 0 0 0 0-4h3.4a8 8 0 0 1 0 4z"/></svg>www.northlinechiro.com</li>
    </ul>
    <div class="person">
      <div class="person-name">DANIEL MERCER</div>
      <div class="person-role">Senior Partner</div>
    </div>
    <div class="edge-tab"></div>
    <svg class="base-band" viewBox="0 0 700 22" preserveAspectRatio="none" aria-hidden="true">
      <polygon points="0,0 498,14 490,22 0,22" fill="var(--blue)"/>
      <polygon points="504,14 700,20 700,22 496,22" fill="var(--graphite)"/>
    </svg>
  </section>
</body>
</html>
```